Start up Dialysis Clinic needs its first website - Velmira Health

Create a visually appealing and user-friendly website for Velmira Health, a dialysis clinic located in Palm Reach, Seabrook. The website should effectively communicate our services to local, regional, and international patients, providing essential information and fostering trust and engagement..
Key Goals:

1. Informative: Provide comprehensive information about our services, facility, and team.
2. User-Friendly: Ensure the website is easy to navigate, with a clear structure and accessible content.
3. Engaging: Create a visually appealing design that reflects the professionalism and care of Velmira Health.
4. Responsive: Ensure the website is fully responsive and performs well on all devices, including desktops, tablets, and smartphones.
5. Trust-Building: Include testimonials, credentials, and patient resources to build trust with potential patients.
Scope of Work:

1. Home Page: An inviting and informative landing page that provides an overview of our clinic, mission, and services. Include a call to action for more information and contact details.
2. About Us: A detailed page about Velmira Health, including our mission, vision, team, and facility tour.
3. Services: A comprehensive page describing the dialysis services we offer, including Hemodialysis, Peritoneal Dialysis, and Home Hemodialysis.
4. Patient Information: A resourceful section with guides for new patients, FAQs, insurance and billing information, and downloadable forms.
5. Resources: Educational content about kidney health, dialysis options, diet and nutrition tips, and support groups.
6. Contact Us: A contact page with our address, phone number, email, office hours, a contact form, and a map.

```html
<!DOCTYPE html>
<html lang="en">
<head>
<meta charset="utf-8">
<title>Velmira Health – Dialysis Clinic, Palm Reach, Seabrook</title>
<link rel="stylesheet" href="https://fonts.googleapis.com/css2?family=Poppins:wght@400;500;600;700&family=Montserrat:wght@400;500;600;700&display=swap">
<style>
:root{
  --blue:#4a7cc3;
  --green:#5b9a5c;
  --footer:#1c3a25;
  --ink:#141414;
  --text:#555;
  --muted:#999;
  --line:#bfc6cc;
  --bg-light:#f4f4f4;
  --white:#fff;
}
*{box-sizing:border-box;margin:0;padding:0}
html,body{width:1200px;height:4284px;overflow:hidden}
body{position:relative;font-family:"Montserrat",sans-serif;color:var(--text);background:var(--white)}
a{text-decoration:none;color:inherit}
.abs{position:absolute}
h1,h2,h3{font-family:"Poppins",sans-serif;color:var(--ink)}

/* header */
.site-header{left:0;top:0;width:1200px;height:86px;background:#efefef;border-top:4px solid var(--green)}
.brand{left:108px;top:0;width:143px;height:110px;background:var(--white);border-radius:0 0 10px 10px;display:flex;flex-direction:column;align-items:center;justify-content:center;gap:8px;box-shadow:0 2px 6px rgba(0,0,0,.08)}
.brand-mark{width:30px;height:30px;background:var(--green)}
.brand-name{font-family:"Poppins",sans-serif;font-weight:600;font-size:17px;color:var(--blue);text-align:center;line-height:1.1}
.main-nav{left:298px;top:38px;display:flex;gap:40px;font-size:13px;font-weight:500;color:#333}
.main-nav .active{color:var(--green);border-bottom:3px solid var(--green);padding-bottom:20px}
.nav-cta{left:920px;top:21px;width:171px;height:46px;background:var(--blue);color:var(--white);font-weight:700;font-size:15px;display:flex;align-items:center;justify-content:center}

/* hero */
.hero{left:0;top:86px;width:1200px;height:597px;background:linear-gradient(180deg,#6c8fc4 0%,#9fb3cf 35%,#b9b4ad 70%,#8e8a86 100%)}
.hero-copy{left:0;top:118px;width:1200px;text-align:center;color:var(--white)}
.hero-copy .kicker{font-family:"Poppins",sans-serif;font-weight:600;font-size:26px}
.hero-copy h1{color:var(--white);font-size:48px;letter-spacing:4px;margin-top:12px}
.hero-copy p{font-size:20px;font-weight:500;margin-top:10px;font-family:"Poppins",sans-serif}
.hero-btn{left:512px;top:293px;width:171px;height:46px;border:2px solid var(--white);color:var(--white);font-weight:700;font-size:15px;display:flex;align-items:center;justify-content:center}

/* about */
.kidney-deco{border-radius:50%;filter:blur(2px);opacity:.55}
.about-title{left:112px;top:790px;font-size:38px;font-weight:700;line-height:1.2}
.about-lead{left:112px;top:855px;width:470px;font-family:"Poppins",sans-serif;font-size:23px;line-height:1.55;color:#444}
.about-text{left:607px;top:775px;width:455px;font-size:15.5px;line-height:30px;color:#444}
.about-text b{color:var(--ink)}
.about-photo-a{left:111px;top:959px;width:446px;height:281px;background:linear-gradient(135deg,#d9dde2,#eef0f2 55%,#c9b8b6)}
.about-photo-b{left:520px;top:1025px;width:537px;height:268px;background:linear-gradient(135deg,#1b2a55,#2f4e8f 55%,#c1502c);border-left:6px solid var(--white);border-top:6px solid var(--white)}

/* services */
.services-title{left:116px;top:1382px;font-size:38px;font-weight:700;line-height:1.2}
.services-intro{left:116px;top:1440px;width:720px;font-size:15.5px;line-height:30px;color:#444}
.service-card{top:1514px;width:400px;height:339px;padding:0 30px 32px;color:var(--white);display:flex;flex-direction:column;justify-content:flex-end}
.service-card.blue{background:linear-gradient(180deg,rgba(74,124,195,.88),rgba(74,124,195,.95))}
.service-card.green{background:linear-gradient(180deg,rgba(106,166,107,.9),rgba(91,154,92,.95))}
.service-card svg{margin-bottom:20px}
.service-card h3{color:var(--white);font-size:19px;font-weight:600;margin-bottom:10px}
.service-card p{font-size:14.5px;line-height:29px;width:270px}

/* testimonials */
.testi-title{left:0;top:1943px;width:1200px;text-align:center;font-size:36px;font-weight:700}
.testi-card{top:2028px;width:313px;height:360px;background:var(--white);border:1px solid #dfe8dc;border-radius:6px;box-shadow:0 3px 10px rgba(0,0,0,.1);text-align:center;padding-top:20px}
.avatar{width:110px;height:110px;border-radius:50%;margin:0 auto}
.testi-card h4{font-family:"Poppins",sans-serif;font-weight:500;font-size:16px;color:var(--ink);margin-top:10px}
.testi-card .role{font-size:13px;color:#333;margin-top:4px}
.quote-mark{position:absolute;left:10px;top:172px;font-family:"Poppins",sans-serif;font-size:34px;font-weight:700;color:#222;line-height:1}
.testi-card p{font-size:13px;line-height:26px;color:var(--muted);padding:22px 22px 0}
.stars{margin-top:6px;display:flex;justify-content:center}
.dots{left:546px;top:2445px;display:flex;gap:14px;align-items:center}
.dot{width:12px;height:12px;border-radius:50%;background:var(--green)}
.dot.current{width:24px;height:24px;border:2px solid var(--green);background:var(--white);display:flex;align-items:center;justify-content:center}
.dot.current::after{content:"";width:14px;height:14px;border-radius:50%;background:var(--green)}

/* mission */
.mission-bg{left:0;top:2543px;width:1200px;height:565px;background:linear-gradient(90deg,#f1f3f6 0%,#eef1f5 50%,#dfe6ee 75%,#c9d3de 100%)}
.mission-box{left:100px;top:2614px;width:453px;height:403px;background:var(--white);border:1px solid #ccc;padding:38px 40px}
.mission-box h2{font-size:32px;font-weight:700}
.mission-box p{font-size:15.5px;line-height:30px;color:#444;margin-top:14px}
.btn{display:inline-flex;align-items:center;justify-content:center;background:var(--blue);color:var(--white);font-weight:700;font-size:15px}
.mission-box .btn{width:172px;height:46px;margin-top:26px}

/* contact */
.contact-bg{left:0;top:3108px;width:1200px;height:703px;background:var(--bg-light)}
.contact-title{left:0;top:3190px;width:1200px;text-align:center;font-size:34px;font-weight:700}
.contact-intro{left:0;top:3258px;width:1200px;text-align:center;font-size:15.5px;line-height:30px;color:#444}
.field{width:420px;border-bottom:2px solid var(--line);padding:0 10px 10px;font-size:14.5px}
.field label{display:block;color:#444;margin-bottom:8px}
.field span{color:var(--muted)}
.field.wide{width:900px;height:128px}
.send-btn{left:512px;top:3670px;width:171px;height:46px}

/* footer */
.site-footer{left:0;top:3811px;width:1200px;height:473px;background:var(--footer)}
.footer-brand{left:110px;top:3935px;display:flex;flex-direction:column;align-items:center;gap:14px}
.footer-brand .brand-mark{width:60px;height:60px;background:var(--white)}
.footer-brand .brand-name{color:var(--white);font-size:30px}
.footer-col{color:var(--white)}
.footer-col h3{color:var(--white);font-family:"Montserrat",sans-serif;font-size:21px;font-weight:600;margin-bottom:22px}
.footer-col li{list-style:none;font-size:16px;line-height:32px}
.contact-list li{display:grid;grid-template-columns:24px 1fr;font-size:14.5px;line-height:28px}
.contact-list svg{margin-top:7px}
.footer-rule{left:110px;top:4233px;width:978px;height:1px;background:#8c9a8e}
.copyright{left:0;top:4245px;width:1200px;text-align:center;font-size:14px;color:var(--white)}
</style>
</head>
<body>

<header class="site-header abs"></header>
<a class="brand abs" href="#" aria-label="Velmira Health home">
  <span class="brand-mark"></span>
  <span class="brand-name">Velmira Health</span>
</a>
<nav class="main-nav abs">
  <span class="active">HOME</span><span>ABOUT US</span><span>SERVICES ▾</span><span>PATIENT INFORMATION</span><span>RESOURCES</span>
</nav>
<a class="nav-cta abs" href="#contact">CONTACT US</a>

<section class="hero abs" role="img" aria-label="Photo of a doctor consulting with a patient at a desk"></section>
<div class="hero-copy abs">
  <div class="kicker">WELCOME TO</div>
  <h1>VELMIRA HEALTH</h1>
  <p>A Dialysis Clinic Located in Palm Reach, Seabrook</p>
</div>
<a class="hero-btn abs" href="#">GET STARTED</a>

<div class="kidney-deco abs" style="left:0;top:700px;width:220px;height:180px;background:radial-gradient(circle,#e6b9a3,#a9c9c4 55%,transparent 75%)" role="img" aria-label="Decorative watercolour kidney illustration"></div>
<h2 class="about-title abs">ABOUT US</h2>
<p class="about-lead abs">Lorem Ipsum is simply dummy text of the printing and typesetting industry.</p>
<p class="about-text abs">Lorem Ipsum is simply dummy text of the printing and typesetting industry. Lorem Ipsum has been the industry's standard dummy text ever since the 1500s, when an unknown printer took a galley of type and scrambled it to make a type specimen book. It has survived not only five centuries, but also the leap into electronic typesetting, remaining essentially unchanged. <b>READ MORE..</b></p>
<div class="about-photo-a abs" role="img" aria-label="Photo of a patient's arm connected to dialysis tubing"></div>
<div class="about-photo-b abs" role="img" aria-label="Photo of a clinician viewing kidney scans on monitors"></div>

<div class="kidney-deco abs" style="left:940px;top:1310px;width:260px;height:205px;background:radial-gradient(circle,#d9a08c,#9ec5c3 55%,transparent 75%)" role="img" aria-label="Decorative watercolour kidney illustration"></div>
<h2 class="services-title abs">EXPLORE OUR SERVICES</h2>
<p class="services-intro abs">Lorem Ipsum is simply dummy text of the printing and typesetting industry. Lorem Ipsum has been the industry's standard dummy text ever since the 1500s,</p>

<article class="service-card blue abs" style="left:0">
  <svg width="56" height="52" viewBox="0 0 56 52" fill="none" stroke="#fff" stroke-width="2.5"><rect x="18" y="3" width="34" height="24" rx="2"/><line x1="35" y1="27" x2="35" y2="34"/><circle cx="10" cy="14" r="5"/><path d="M4 46V28a6 6 0 0 1 12 0v10h14v8z"/></svg>
  <h3>Hemodialysis</h3>
  <p>Lorem Ipsum is simply dummy text of the printing and typesetting industry. <b>Learn More..</b></p>
</article>
<article class="service-card green abs" style="left:400px">
  <svg width="56" height="52" viewBox="0 0 56 52" fill="none" stroke="#fff" stroke-width="2.5"><rect x="18" y="3" width="34" height="24" rx="2"/><line x1="35" y1="27" x2="35" y2="34"/><circle cx="10" cy="14" r="5"/><path d="M4 46V28a6 6 0 0 1 12 0v10h14v8z"/></svg>
  <h3>Peritoneal Dialysis</h3>
  <p>Lorem Ipsum is simply dummy text of the printing and typesetting industry. <b>Learn More..</b></p>
</article>
<article class="service-card blue abs" style="left:800px">
  <svg width="56" height="52" viewBox="0 0 56 52" fill="none" stroke="#fff" stroke-width="2.5"><rect x="18" y="3" width="34" height="24" rx="2"/><line x1="35" y1="27" x2="35" y2="34"/><circle cx="10" cy="14" r="5"/><path d="M4 46V28a6 6 0 0 1 12 0v10h14v8z"/></svg>
  <h3>Home Hemodialysis</h3>
  <p>Lorem Ipsum is simply dummy text of the printing and typesetting industry. <b>Learn More..</b></p>
</article>

<h2 class="testi-title abs">WHAT OUR CLIENTS SAY</h2>
<article class="testi-card abs" style="left:110px">
  <div class="avatar" style="background:linear-gradient(135deg,#f6c4a0,#e89a6e)" role="img" aria-label="Client portrait"></div>
  <h4>Anderson</h4><div class="role">Client</div><span class="quote-mark">“</span>
  <p>Lorem Ipsum is simply dummy text of the printing and typesetting industry. Lorem Ipsum has been the industry's standard dummy text ever since the</p>
  <div class="stars"><svg width="90" height="16" viewBox="0 0 90 16" fill="#f2b705"><g id="s"><polygon points="8,0 10,6 16,6 11,10 13,16 8,12 3,16 5,10 0,6 6,6"/></g><use href="#s" x="18"/><use href="#s" x="36"/><use href="#s" x="54"/><use href="#s" x="72"/></svg></div>
</article>
<article class="testi-card abs" style="left:442px">
  <div class="avatar" style="background:linear-gradient(135deg,#dfe3e8,#b8c3cf)" role="img" aria-label="Client portrait"></div>
  <h4>Robin</h4><div class="role">Client</div><span class="quote-mark">“</span>
  <p>Lorem Ipsum is simply dummy text of the printing and typesetting industry. Lorem Ipsum has been the industry's standard dummy text ever since the</p>
  <div class="stars"><svg width="90" height="16" viewBox="0 0 90 16" fill="#f2b705"><use href="#s"/><use href="#s" x="18"/><use href="#s" x="36"/><use href="#s" x="54"/><use href="#s" x="72"/></svg></div>
</article>
<article class="testi-card abs" style="left:773px">
  <div class="avatar" style="background:linear-gradient(135deg,#eeeeee,#d6d0cb)" role="img" aria-label="Client portrait"></div>
  <h4>Jessica</h4><div class="role">Client</div><span class="quote-mark">“</span>
  <p>Lorem Ipsum is simply dummy text of the printing and typesetting industry. Lorem Ipsum has been the industry's standard dummy text ever since the</p>
  <div class="stars"><svg width="90" height="16" viewBox="0 0 90 16" fill="#f2b705"><use href="#s"/><use href="#s" x="18"/><use href="#s" x="36"/><use href="#s" x="54"/><use href="#s" x="72"/></svg></div>
</article>
<div class="dots abs"><span class="dot current"></span><span class="dot"></span><span class="dot"></span><span class="dot"></span></div>

<section class="mission-bg abs" role="img" aria-label="Photo of two clinicians reviewing a clipboard"></section>
<div class="mission-box abs">
  <h2>OUR MISSION</h2>
  <p>Lorem Ipsum is simply dummy text of the printing and typesetting industry. Lorem Ipsum has been the industry's standard dummy text ever since the 1500s, when an unknown printer took a galley of type and scrambled it to make a</p>
  <a class="btn" href="#">READ MORE</a>
</div>

<section id="contact" class="contact-bg abs"></section>
<div class="kidney-deco abs" style="left:0;top:3110px;width:280px;height:220px;background:radial-gradient(circle,#c89ad8,#b4c2e6 55%,transparent 75%)" role="img" aria-label="Decorative watercolour kidney illustration"></div>
<div class="kidney-deco abs" style="left:910px;top:3590px;width:290px;height:220px;background:radial-gradient(circle,#e29ad0,#a8d0e4 55%,transparent 75%)" role="img" aria-label="Decorative watercolour kidney illustration"></div>
<h2 class="contact-title abs">CONTACT US</h2>
<p class="contact-intro abs">Lorem Ipsum is simply dummy text of the printing and typesetting industry.<br>Lorem Ipsum has been the industry's standard dummy text ever since the 1500s, when an unknown</p>
<div class="field abs" style="left:146px;top:3330px"><label>Your Name</label><span>First Name</span></div>
<div class="field abs" style="left:627px;top:3330px"><label>Email Address</label><span>@mail.com</span></div>
<div class="field abs" style="left:146px;top:3421px"><label>Phone</label><span>123-456-7890</span></div>
<div class="field abs" style="left:627px;top:3421px"><label>Subject</label><span>Dialysis</span></div>
<div class="field wide abs" style="left:146px;top:3523px"><label>Message</label><span>Type Here</span></div>
<a class="btn send-btn abs" href="#">SEND MESSAGE</a>

<footer class="site-footer abs"></footer>
<div class="footer-brand abs"><span class="brand-mark"></span><span class="brand-name">Velmira Health</span></div>
<div class="footer-col abs" style="left:380px;top:3898px">
  <h3>MAIN LINKS</h3>
  <ul><li>Home</li><li>About Us</li><li>Services</li><li>Patient Information</li><li>Resources</li><li>Contact Us</li></ul>
</div>
<div class="footer-col abs" style="left:605px;top:3898px">
  <h3>OTHER LINKS</h3>
  <ul><li>Terms and Conditions</li><li>Security</li><li>Privacy Policy</li></ul>
</div>
<div class="footer-col abs" style="left:869px;top:3898px">
  <h3>CONTACT</h3>
  <ul class="contact-list">
    <li><svg width="14" height="14" viewBox="0 0 24 24" fill="#fff"><path d="M6.6 10.8a15 15 0 0 0 6.6 6.6l2.2-2.2c.3-.3.7-.4 1-.2 1.1.4 2.3.6 3.6.6.6 0 1 .4 1 1V20c0 .6-.4 1-1 1A17 17 0 0 1 3 4c0-.6.4-1 1-1h3.5c.6 0 1 .4 1 1 0 1.3.2 2.5.6 3.6.1.3 0 .7-.2 1z"/></svg><span><b>Call Us</b><br>+1 868 555 0142</span></li>
    <li><svg width="14" height="14" viewBox="0 0 24 24" fill="#fff"><path d="M2 5h20v14H2z M2 5l10 8 10-8" stroke="#1c3a25" stroke-width="1.5"/></svg><span><b>Mail Us</b><br>info@velmirahealth.com</span></li>
    <li><svg width="14" height="16" viewBox="0 0 24 28" fill="#fff"><path d="M12 0a9 9 0 0 0-9 9c0 7 9 19 9 19s9-12 9-19a9 9 0 0 0-9-9zm0 13a4 4 0 1 1 0-8 4 4 0 0 1 0 8z"/></svg><span><b>Location</b><br>Palm Reach,<br>Seabrook</span></li>
    <li><svg width="14" height="14" viewBox="0 0 24 24"><circle cx="12" cy="12" r="11" fill="#fff"/><path d="M12 6v6l4 3" stroke="#1c3a25" stroke-width="2.5" fill="none"/></svg><span><b>Working Hours</b><br>Mon - Sat 9:00 To 5:00 PM</span></li>
  </ul>
</div>
<div class="footer-rule abs"></div>
<p class="copyright abs">© 2024 Velmira Health | All Rights Reserved</p>

</body>
</html>
```